Dalvick's Business Card

I need some designs for a new business card including the new logo attached. An old example of our business card is also attached to show all the data that should be included on the new design.
**I added some more examples someone had mocked up**

Contact Information for Business Card

Should include all info on other examples uploaded.

```html
<!DOCTYPE html>
<html lang="en">
<head>
<meta charset="utf-8">
<title>Dalvick's Business Card</title>
<link rel="stylesheet" href="https://fonts.googleapis.com/css2?family=Montserrat:wght@400;500;600;700&display=swap">
<style>
  :root {
    --bg: #ababab;
    --card: #ffffff;
    --brand-blue: #0a6fba;
    --brand-red: #e3202a;
    --band-red: #d0273a;
    --band-blue: #1f67b0;
    --text-grey: #6a6a6a;
    --rule-grey: #d9d9d9;
  }
  * { margin: 0; padding: 0; box-sizing: border-box; }
  html, body { width: 1200px; height: 1000px; overflow: hidden; }
  body {
    background: var(--bg);
    position: relative;
    font-family: "Montserrat", sans-serif;
  }
  .card {
    position: absolute;
    left: 294px;
    width: 613px;
    height: 352px;
    background: var(--card);
    border-radius: 26px;
    overflow: hidden;
  }
  .card--front { top: 96px; }
  .card--back { top: 528px; }

  .front-mark {
    position: absolute;
    left: 262px; top: 64px;
    width: 88px; height: 88px;
    border-radius: 50%;
    background: var(--brand-blue);
  }
  .brand-name {
    color: var(--brand-blue);
    font-weight: 700;
    line-height: 1;
    white-space: nowrap;
  }
  .brand-tagline {
    color: var(--brand-red);
    font-weight: 700;
    white-space: nowrap;
    line-height: 1;
  }
  .front-brand {
    position: absolute;
    left: 0; right: 0; top: 198px;
    text-align: center;
  }
  .front-brand .brand-name { font-size: 61px; letter-spacing: 0.5px; }
  .front-brand .brand-tagline { font-size: 15.5px; margin-top: 6px; }

  .front-band {
    position: absolute;
    left: 0; right: 0; bottom: 0;
    height: 40px;
    background: linear-gradient(90deg, var(--band-red) 0%, #8a3f6a 45%, var(--band-blue) 100%);
    color: #fff;
    font-weight: 600;
    font-size: 15px;
    display: flex;
    align-items: center;
    padding-left: 124px;
    letter-spacing: 0.2px;
  }
  .front-band .divider { margin: 0 18px 0 10px; }

  .back-brand {
    position: absolute;
    left: 35px; top: 46px;
  }
  .back-brand .brand-name { font-size: 35px; }
  .back-brand .brand-tagline { font-size: 9.6px; margin-top: 3px; }

  .person-name {
    position: absolute;
    left: 36px; top: 169px;
    color: var(--brand-blue);
    font-size: 22px;
    font-weight: 500;
  }
  .name-rule {
    position: absolute;
    left: 36px; top: 206px;
    width: 146px; height: 2px;
    background: var(--rule-grey);
  }
  .contact-list {
    position: absolute;
    left: 34px; top: 226px;
    list-style: none;
    color: var(--text-grey);
    font-size: 13px;
    letter-spacing: 0.5px;
    line-height: 17px;
  }
  .contact-item { display: flex; align-items: flex-start; }
  .contact-item svg { width: 12px; height: 12px; margin-right: 6px; margin-top: 3px; flex: none; fill: var(--brand-red); }
  .contact-item--address { margin-bottom: 18px; }
</style>
</head>
<body>

<section class="card card--front" aria-label="Card front">
  <div class="front-mark" aria-hidden="true"></div>
  <div class="front-brand">
    <div class="brand-name">DALVICK'S</div>
    <div class="brand-tagline">AIR CONDITIONING &amp; HEATING SERVICE</div>
  </div>
  <div class="front-band">
    <span>LICENSED &amp; INSURED</span><span class="divider">|</span><span>FAMILY OWNED &amp; OPERATED</span>
  </div>
</section>

<section class="card card--back" aria-label="Card back">
  <div class="back-brand">
    <div class="brand-name">DALVICK'S</div>
    <div class="brand-tagline">AIR CONDITIONING &amp; HEATING SERVICE</div>
  </div>
  <div class="person-name">Nolan Dalvick</div>
  <div class="name-rule"></div>
  <ul class="contact-list">
    <li class="contact-item contact-item--address">
      <svg viewBox="0 0 12 12" aria-hidden="true"><path d="M6 0.5a4 4 0 0 0-4 4c0 3 4 7 4 7s4-4 4-7a4 4 0 0 0-4-4zm0 5.6a1.6 1.6 0 1 1 0-3.2 1.6 1.6 0 0 1 0 3.2z"/></svg>
      <span>418 Maplecrest Avenue<br>Ridgeford, IA 50217, EUA</span>
    </li>
    <li class="contact-item">
      <svg viewBox="0 0 12 12" aria-hidden="true"><path d="M3 1.5l1.8 2.4-1 1.2c.7 1.4 1.7 2.4 3.1 3.1l1.2-1 2.4 1.8-.9 1.6C5.6 10.5 1.5 6.4 1.4 2.4z"/></svg>
      <span>555.014.2288</span>
    </li>
    <li class="contact-item">
      <svg viewBox="0 0 12 12" aria-hidden="true"><path d="M1 3h10v6H1z M1 3l5 3.5L11 3" stroke="#fff" stroke-width="0.8"/></svg>
      <span>hvacdalvick@mailbox.com</span>
    </li>
  </ul>
</section>

</body>
</html>
```